Dental Business Card Design w/logo

Classic, elegant w/a touch of contemporary
Upscale dental facility located in Modesto CA
Specializing in restorative & general dentistry
Providing exceptional customer service to the community
Updates

I prefer script and not bold writing
If you can use the phone; fax and email icons instead of spelling them out, it would be great
No bold colors
Classy and elegant
In the back of the card I would like to see something like this
Your Next Appointment:
Mon     Tue    Wed    Thur (a box next to each of them for marking)
Date:_______________ at_____________ AM    PM  (a box next to them for marking)

Thank you

Target Market(s)

Well established professional

Industry/Entity Type

Dental

Contact Information for Business Card

Velarina Tossudi DMD
4176 Marlow Rd
Suite K7
Modesto, CA 95418

Office: 209-731-5920
Fax: 209-731-8047
Email: tossudidmd@quillmail.example

Requirements
Must have
• Unique classic logo
An easily repeatable design that can be used on letterhead and envelopes
Nice to have
• My initials incorporated into unique design
Should not have
• No cartoons or cheesy themes. This is a practice for the well established and professional individual.

```html
<!DOCTYPE html>
<html lang="en">
<head>
<meta charset="utf-8">
<title>Velarina Tossudi DMD – Business Card</title>
<link rel="stylesheet" href="https://fonts.googleapis.com/css2?family=Jost:ital,wght@0,400;1,400&display=swap">
<style>
  :root {
    --page-bg: #ffffff;
    --card-bg: #ffffff;
    --card-edge: #333333;
    --slate: #5b6a74;
    --ink: #111111;
    --teal: #3f9698;
  }
  * { box-sizing: border-box; margin: 0; padding: 0; }
  html, body {
    width: 1200px; height: 900px; overflow: hidden;
    background: var(--page-bg);
    font-family: "Jost", "Futura", sans-serif;
  }
  .card {
    position: absolute; left: 343px; top: 14px;
    width: 508px; height: 866px;
    background: var(--card-bg);
    border: 1px solid var(--card-edge);
  }
  .practice-name {
    position: absolute; left: 42px; top: 172px;
    font-size: 63px; line-height: 70px; font-weight: 400;
    color: var(--slate); letter-spacing: 0.5px;
  }
  .practice-name .degree {
    display: block; text-align: right;
    font-size: 31px; line-height: 40px; padding-right: 6px;
  }
  .specialty {
    position: absolute; left: 48px; top: 352px; width: 310px;
    font-style: italic; font-size: 25px; line-height: 30px;
    color: var(--ink); text-align: center;
  }
  .address {
    position: absolute; left: 0; top: 573px; width: 100%;
    font-style: normal; font-size: 29px; line-height: 37px;
    color: var(--slate); text-align: center; padding-left: 14px;
  }
  .contact {
    position: absolute; left: 0; top: 682px; width: 100%;
    list-style: none; font-size: 25px; line-height: 36px;
    color: var(--slate);
  }
  .contact li {
    display: flex; justify-content: center; align-items: center; gap: 8px;
  }
  .contact li.phone, .contact li.fax { padding-left: 64px; }
  .contact svg { display: block; }
</style>
</head>
<body>
  <main class="card">
    <h1 class="practice-name">VELARINA<br>TOSSUDI<span class="degree">DMD</span></h1>
    <p class="specialty">GENERAL &amp; RESTORATIVE DENTISTRY</p>

    <address class="address">4176 Marlow Rd Suite K7<br>Modesto, CA 95418</address>

    <ul class="contact">
      <li class="phone">
        <svg width="24" height="30" viewBox="0 0 24 30" aria-label="Phone">
          <path d="M6 2 L10 2 L11 9 L8 11 Q9 18 13 22 L16 20 L21 24 L19 28 Q10 29 5 17 Q2 8 6 2 Z" fill="var(--teal)"/>
        </svg>
        <span>209-731-5920</span>
      </li>
      <li class="fax">
        <svg width="34" height="30" viewBox="0 0 34 30" aria-label="Fax">
          <rect x="9" y="2" width="16" height="12" fill="#ffffff" stroke="var(--slate)" stroke-width="1.5"/>
          <rect x="2" y="12" width="30" height="16" rx="2" fill="var(--slate)"/>
          <rect x="6" y="16" width="16" height="3" fill="#ffffff"/>
          <rect x="25" y="16" width="4" height="4" fill="var(--teal)"/>
        </svg>
        <span>209-731-8047</span>
      </li>
      <li class="email">
        <svg width="36" height="26" viewBox="0 0 36 26" aria-label="Email">
          <rect x="1" y="2" width="34" height="22" rx="1" fill="var(--teal)"/>
          <text x="18" y="19" font-size="15" fill="#ffffff" text-anchor="middle" font-family="Jost, sans-serif">@</text>
        </svg>
        <span>tossudidmd@quillmail.example</span>
      </li>
    </ul>
  </main>
</body>
</html>
```